Wizards in Fibbing Crafts*

I am looking for a book cover which will really pop. Working title: Wizards in Fibbing Crafts (or W.F.C. for short) The concept behind the book is: education is too expensive, screwed up, and basically failing us, and even an MBA is not worth it's name anymore! How a BS is Brilliantly Stupid, a BA is great to be a Broke Artist, an MA is Mostly Antiquated and a MS Mastered Something? ...you get the point, basically I'll be ripping into a whole bunch of degree types, then walking you through what you should actually learn from an MBA. It is going to be written with a fair bit of humor, while still being fact driven. Target audience is working professionals who are considering an MBA, or have one and want a $15 refresher of all they spent $90k+ on. No color scheme is requested, Since i do like to allow creativity to flow!

Book size 5" by 8" and ebook. Author is: R.T. Halvorsen size format attached.

Went on vacation/holiday

• W.F.C. (but can be an emphasises in the Wizards in Fibbing Crafts title.
• If you look at "Side hustle blueprint: a guide toward cash liberty alongside a steady day job" on shopvale, you can see a blue/silver/white color scheme I liked in the past - but dont take that as a must by any means, the second choice was a completely different (red and white) scheme

```html
<!DOCTYPE html>
<html lang="en">
<head>
<meta charset="utf-8">
<title>Wizards in Fibbing Crafts — Book Cover</title>
<link href="https://fonts.googleapis.com/css2?family=Archivo+Black&family=Bebas+Neue&family=Libre+Baskerville&family=Roboto:wght@700;900&display=swap" rel="stylesheet">
<style>
  :root {
    --backdrop: #e8e8e8;
    --paper: #ffffff;
    --navy: #0b3577;
    --steel-blue: #4b6f9f;
    --signal-red: #ec1c24;
    --mascot-brown: #8b6a53;
    --mascot-label: #f4ece6;
    --ink: #1b1b1b;
  }
  html, body {
    margin: 0;
    padding: 0;
    width: 1200px;
    height: 800px;
    overflow: hidden;
    background: var(--backdrop);
  }
  .stage {
    position: relative;
    width: 1200px;
    height: 800px;
  }
  .book-cover {
    position: absolute;
    left: 346px;
    top: 20px;
    width: 508px;
    height: 760px;
    display: block;
    box-shadow: 0 6px 24px rgba(0, 0, 0, 0.18);
  }
  .cover-paper { fill: var(--paper); }
  .title-top {
    font-family: "Archivo Black", "Roboto", sans-serif;
    font-size: 100px;
  }
  .title-top .tone-dark { fill: var(--navy); }
  .title-top .tone-light { fill: var(--steel-blue); }
  .title-joiner {
    font-family: "Roboto", sans-serif;
    font-weight: 900;
    font-size: 40px;
    fill: var(--navy);
  }
  .title-rule { stroke: var(--navy); stroke-width: 2; }
  .title-red {
    font-family: "Bebas Neue", sans-serif;
    fill: var(--signal-red);
  }
  .title-fibbing { font-size: 121px; }
  .title-crafts { font-size: 214px; }
  .mascot-art { fill: var(--mascot-brown); }
  .mascot-label {
    font-family: "Roboto", sans-serif;
    font-weight: 700;
    font-size: 34px;
    fill: var(--mascot-label);
  }
  .author-name {
    font-family: "Libre Baskerville", serif;
    font-size: 36px;
    fill: var(--ink);
  }
</style>
</head>
<body>
<main class="stage">
  <svg class="book-cover" viewBox="0 0 590 882" xmlns="http://www.w3.org/2000/svg" aria-label="Book cover: Wizards in Fibbing Crafts by R.T. Halvorsen">
    <rect class="cover-paper" x="0" y="0" width="590" height="882"/>

    <rect class="mascot-art" x="128" y="504" width="334" height="286" rx="150" ry="125" role="img" aria-label="Cartoon mascot illustration with googly eyes carrying the W.F.C. label"/>
    <text class="mascot-label" x="302" y="572" text-anchor="middle">W.F.C.</text>

    <text class="title-top" x="59" y="158" textLength="470" lengthAdjust="spacingAndGlyphs"><tspan class="tone-dark">WIZA</tspan><tspan class="tone-light">RDS</tspan></text>

    <line class="title-rule" x1="57" y1="195" x2="238" y2="195"/>
    <line class="title-rule" x1="352" y1="195" x2="545" y2="195"/>
    <text class="title-joiner" x="295" y="208" text-anchor="middle">IN</text>

    <text class="title-red title-fibbing" x="52" y="318" textLength="497" lengthAdjust="spacingAndGlyphs">FIBBING</text>
    <text class="title-red title-crafts" x="78" y="490" textLength="434" lengthAdjust="spacingAndGlyphs">CRAFTS</text>

    <text class="author-name" x="68" y="848" textLength="453" lengthAdjust="spacing">R.T. HALVORSEN</text>
  </svg>
</main>
</body>
</html>
```